GTP biz card

We need a business card design for our new company based in Los Angeles called "Gold Tide Pictures". We develop film and television projects. We work with investors, financiers, film production companies, film distribution and sales companies as well as studios. We would like to incorporate our logo (see attached) on a two-sided card. We need to include: name and title, address, phone, email and company website.

Target Market(s)

Business, financial and studio clients

Industry/Entity Type

Business

Contact Information for Business Card

Two-sided. We are thinking of the logo on one side and the information on the back. Please feel free to be creative! Thanks.

Requirements
Must have
• Please include the following text information, excluding the "CAPS CATEGORY:" and please allow the ability for us to change the name, title and email address for each company employee):
• NAME & TITLE:
• Neil Parker
• Managing Partner
• COMPANY NAME:
• GOLD TIDE PICTURES (please use existing logo)
• COMPANY ADDRESS:
• KTW Studio Park
• 2250 Halverd Street
• Harbor Wing, 4th Floor
• Manhattan Beach, CA 90412
• COMPANY PHONE NUMBER:
• 310-555-0148
• COMPANY WEBSITE ADDRESS:
• www.goldtidepicturesgroup.example
• EMAIL ADDRESS: (only one per card)
• peter@goldtidepicturesgroup.example
• bingo@goldtidepicturesgroup.example
• neil@goldtidepicturesgroup.example

```html
<!DOCTYPE html>
<html lang="en">
<head>
<meta charset="utf-8">
<title>Gold Tide Pictures – Business Card</title>
<link href="https://fonts.googleapis.com/css2?family=Exo+2:wght@300;600&family=Arimo:wght@400&display=swap" rel="stylesheet">
<style>
  :root {
    --bg: #5b5b5d;
    --card: #020203;
    --cyan: #2ec8f2;
    --cyan-deep: #1697c4;
    --cyan-light: #c9f1fb;
  }
  html, body {
    margin: 0;
    width: 1200px;
    height: 900px;
    overflow: hidden;
    background: var(--bg);
  }
  .canvas {
    position: relative;
    width: 1200px;
    height: 900px;
  }
  .card {
    position: absolute;
    width: 560px;
    height: 320px;
    background: var(--card);
    box-shadow: 0 10px 28px rgba(0,0,0,0.45);
    overflow: hidden;
  }
  .card-front { left: 60px; top: 110px; }
  .card-back  { left: 580px; top: 470px; }

  .accent-line {
    position: absolute;
    height: 7px;
    background: linear-gradient(90deg, var(--cyan-deep), var(--cyan) 40%, var(--cyan-light) 75%, var(--cyan));
  }
  .card-front .line-left  { left: 0; width: 205px; top: 168px; }
  .card-front .line-right { right: 0; width: 205px; top: 168px;
    background: linear-gradient(90deg, var(--cyan), var(--cyan-light) 40%, var(--cyan) 70%, var(--cyan-deep)); }

  .brand-dot {
    position: absolute;
    border-radius: 50%;
    background: radial-gradient(circle at 50% 45%, var(--cyan-light), var(--cyan) 45%, #0a4e66 100%);
  }
  .card-front .brand-dot { width: 110px; height: 110px; left: 225px; top: 117px; }

  .brand-name {
    position: absolute;
    left: 0; right: 0;
    top: 250px;
    margin: 0;
    text-align: center;
    font-family: "Exo 2", sans-serif;
    font-weight: 600;
    font-size: 36px;
    letter-spacing: 3px;
    color: var(--cyan);
  }

  .card-back .brand-dot { width: 46px; height: 46px; left: 90px; top: 14px; }
  .card-back .name-line { left: 0; right: 0; top: 112px; }
  .person-name {
    position: absolute;
    left: 36px; top: 60px;
    margin: 0;
    font-family: "Exo 2", sans-serif;
    font-weight: 300;
    font-size: 40px;
    line-height: 48px;
    letter-spacing: 1px;
    color: var(--cyan);
  }
  .person-title {
    position: absolute;
    left: 36px; top: 132px;
    margin: 0;
    font-family: "Arimo", sans-serif;
    font-size: 15px;
    line-height: 18px;
    letter-spacing: 1px;
    text-transform: uppercase;
    color: var(--cyan);
  }
  .contact {
    position: absolute;
    left: 36px; top: 166px;
    margin: 0;
    font-family: "Arimo", sans-serif;
    font-style: normal;
    font-size: 14px;
    line-height: 18px;
    color: var(--cyan);
  }
</style>
</head>
<body>
<main class="canvas">
  <section class="card card-front" aria-label="Card front">
    <div class="accent-line line-left"></div>
    <div class="accent-line line-right"></div>
    <div class="brand-dot"></div>
    <h1 class="brand-name">GOLD TIDE PICTURES</h1>
  </section>

  <section class="card card-back" aria-label="Card back">
    <div class="brand-dot"></div>
    <h2 class="person-name">Neil Parker</h2>
    <div class="accent-line name-line"></div>
    <p class="person-title">Managing Partner</p>
    <address class="contact">
      KTW Studio Park<br>
      2250 Halverd Street<br>
      Harbor Wing, 4th Floor<br>
      Manhattan Beach, CA 90412<br>
      Phone: 310-555-0148<br>
      Email: neil@goldtidepicturesgroup.example<br>
      www.goldtidepicturesgroup.example
    </address>
  </section>
</main>
</body>
</html>
```